Business Card Design

We are a law firm which provides services to creditors.....we do collection litigation. I am wide open on suggestions. I was thinking of a square card? Alternatively, a vertically oriented standard card or a folded card.....something unique. I would like to use my firm logo and beyond that, I am open for any and all suggestions. I'm uncertain if the complete log is uploaded? If not, please let me email it to you.

Industry/Entity Type

Law Firm

Contact Information for Business Card

Hart, Crane & Dobbs, P.C.
Tom Dobbs, Lawyer
4387 N Larkspur Ave
Oklahoma City, OK 73924
tdobbs@HcdCounsel.com
www.HcdCounsel.com
mobile: 405-382-7914

```html
<!DOCTYPE html>
<html lang="en">
<head>
<meta charset="utf-8">
<title>Hart, Crane &amp; Dobbs, P.C. – Business Card</title>
<link href="https://fonts.googleapis.com/css2?family=Arimo:wght@400;700&display=swap" rel="stylesheet">
<style>
  :root {
    --green: #0f6e38;
    --green-dark: #0a5a2c;
    --green-light: #2f8a4f;
    --gold: #b9a236;
    --gold-light: #cbb54c;
    --paper: #ffffff;
    --backdrop: #ece8df;
  }
  html, body {
    margin: 0;
    padding: 0;
    width: 1200px;
    height: 892px;
    overflow: hidden;
    background: var(--backdrop);
    font-family: "Arimo", Arial, sans-serif;
  }
  .canvas {
    position: relative;
    width: 1200px;
    height: 892px;
  }
  .card {
    position: absolute;
    width: 560px;
    height: 320px;
    box-shadow: 0 6px 18px rgba(0,0,0,0.18);
  }
  .card-bg {
    position: absolute;
    inset: 0;
  }
  .card--front { left: 580px; top: 70px; }
  .card--back  { left: 60px;  top: 500px; }

  .firm-name {
    position: absolute;
    margin: 0;
    color: var(--green);
    font-weight: 700;
    letter-spacing: 0.5px;
    white-space: nowrap;
  }
  .card--front .firm-name {
    left: 0;
    right: 0;
    top: 208px;
    text-align: center;
    font-size: 34px;
  }
  .card--back .firm-name {
    left: 52px;
    top: 38px;
    font-size: 32px;
  }

  .brand-mark {
    position: absolute;
    display: flex;
    align-items: center;
    gap: 8px;
    color: var(--green);
    font-weight: 700;
    font-size: 15px;
    white-space: nowrap;
  }
  .brand-mark__dot {
    width: 26px;
    height: 26px;
    border-radius: 50%;
    background: var(--gold);
  }
  .card--front .brand-mark { left: 200px; top: 130px; }
  .card--back .brand-mark  { left: 318px; top: 236px; }

  .person {
    position: absolute;
    left: 52px;
    top: 82px;
    color: var(--green);
  }
  .person__name {
    margin: 0;
    font-weight: 400;
    font-size: 30px;
    line-height: 1;
  }
  .person__role {
    margin: 2px 0 0;
    font-size: 10px;
  }
  .contact {
    position: absolute;
    left: 52px;
    top: 146px;
    margin: 0;
    padding: 0;
    list-style: none;
    color: var(--green);
    font-size: 14px;
    line-height: 21px;
  }
</style>
</head>
<body>
<main class="canvas">

  <!-- Front of card -->
  <section class="card card--front" aria-label="Card front">
    <svg class="card-bg" width="560" height="320" viewBox="0 0 560 320" aria-hidden="true">
      <rect width="560" height="320" fill="var(--gold)"/>
      <rect x="60" y="24" width="470" height="266" fill="var(--paper)"/>
      <polygon points="0,110 60,24 60,290 200,290 170,320 0,320" fill="var(--green-dark)"/>
      <polygon points="200,290 530,290 530,320 170,320" fill="var(--gold-light)"/>
      <polygon points="420,0 560,0 560,140 530,110 530,24 470,24" fill="var(--green-light)"/>
    </svg>
    <div class="brand-mark">
      <span class="brand-mark__dot"></span>
      <span>Hart, Crane &amp; Dobbs</span>
    </div>
    <h1 class="firm-name">Hart, Crane &amp; Dobbs, P.C.</h1>
  </section>

  <!-- Back of card -->
  <section class="card card--back" aria-label="Card back">
    <svg class="card-bg" width="560" height="320" viewBox="0 0 560 320" aria-hidden="true">
      <rect width="560" height="320" fill="var(--gold)"/>
      <rect x="28" y="24" width="504" height="272" fill="var(--paper)"/>
      <polygon points="0,0 300,0 250,24 70,24 28,70 28,120 0,140" fill="var(--green)"/>
      <polygon points="300,0 330,0 290,24 250,24" fill="var(--gold-light)"/>
      <polygon points="370,320 560,320 560,200 532,228 532,296 400,296" fill="var(--green-light)"/>
    </svg>
    <h2 class="firm-name">Hart, Crane &amp; Dobbs, P.C.</h2>
    <div class="person">
      <p class="person__name">Tom Dobbs</p>
      <p class="person__role">Lawyer</p>
    </div>
    <ul class="contact">
      <li>405-382-7914</li>
      <li>www.HcdCounsel.com</li>
      <li>tdobbs@HcdCounsel.com</li>
      <li>4387 N Larkspur Ave Oklahoma City,<br>OK 73924</li>
    </ul>
    <div class="brand-mark">
      <span class="brand-mark__dot"></span>
      <span>Hart, Crane &amp; Dobbs</span>
    </div>
  </section>

</main>
</body>
</html>
```